Web landing page design

- Create a Web Design (Uncoded - PSD layout only)

We need a single web page design to promote our service. This page will
acts as a landing page for users and also be utilized in social media
advertising. Please provide us with a cutting edge design. I have attached
a link for what the company is about. In essence we are a photo checking
service which reviews photos for retailers, hotels abd car dealerships to
check everything is good after a service has been performed. Whether it be
a new promotion, cleaning or just checking prices. I am looking for a
design to say that we do many photos and at a very cost effective price
(team based in Mexico)

Link: https://slidevault.example/view/qTr8nWx2LpZk4mHcYdJs/
*Deadline*
5 days
*Updates*

- The Start Here box needs to look like this:

-Start Here (heading)
-A box for email addresses to be entered
-Then a check box with "Yes, I have read and agree to the Privacy Policy
and agree to receive email marketing from Plumora88'
-A submit button

All of this information needs to be in one box please. And please feel
free to contact me if you have any questions about this.

*Target Market(s)*
Retail business, Merchandising companies, Rental property owners, Car
dealers
Updates

Please can you submit entries. I am just looking for a tidy to a presentation already created. Just needs design touches.

Target Market(s)

Ability for audience to understand concept quickly
Benefits to why to use the product stand out
Technology driven approach

Industry/Entity Type

Retail

Number of Pages Required

1 page

Colors
0792cd

Requirements
Must have
• Clean and modern design

```html
<!DOCTYPE html>
<html lang="en">
<head>
<meta charset="utf-8">
<title>plumora — Photo Review Landing Page</title>
<link rel="stylesheet" href="https://fonts.googleapis.com/css2?family=Lato:ital,wght@0,400;0,700;0,900;1,400&display=swap">
<style>
  :root {
    --brand-blue: #1580c4;
    --accent-blue: #1a8fd6;
    --cta-orange: #d9731f;
    --ink: #2b2b2b;
    --white: #ffffff;
    --hero-dark: #2a2a2e;
  }
  * { box-sizing: border-box; margin: 0; padding: 0; }
  html, body { width: 1200px; height: 853px; overflow: hidden; }
  body { font-family: "Lato", sans-serif; background: var(--white); position: relative; }

  .hero { position: absolute; left: 0; top: 0; width: 1200px; height: 561px; overflow: hidden; }
  .hero-photo {
    position: absolute; inset: 0;
    background:
      radial-gradient(ellipse 380px 420px at 930px 230px, rgba(110,150,150,0.55), transparent 70%),
      radial-gradient(ellipse 500px 300px at 250px 380px, rgba(120,110,120,0.5), transparent 70%),
      linear-gradient(180deg, #3c3d45 0%, #45464c 45%, #3a3a3c 100%);
  }
  .hero-shade { position: absolute; inset: 0; background: rgba(0,0,0,0.25); }

  .brand { position: absolute; display: flex; flex-direction: column; align-items: center; color: var(--white); }
  .brand-dot { width: 24px; height: 24px; border-radius: 50%; background: var(--accent-blue); margin-bottom: 4px; }
  .brand-name { font-weight: 700; font-size: 27px; letter-spacing: 0.5px; line-height: 1; }
  .hero .brand { left: 76px; top: 28px; }

  .main-nav { position: absolute; right: 74px; top: 46px; display: flex; align-items: center; gap: 26px; }
  .main-nav a { color: var(--white); text-decoration: none; font-size: 13px; font-weight: 700; letter-spacing: 0.3px; }
  .main-nav .nav-trial { background: var(--brand-blue); padding: 10px 18px; border-radius: 18px; }

  .signup { position: absolute; left: 0; top: 210px; width: 1200px; display: flex; flex-direction: column; align-items: center; color: var(--white); }
  .signup-title { font-size: 38px; font-weight: 900; letter-spacing: 0.5px; line-height: 1; }
  .email-field {
    margin-top: 26px; width: 568px; height: 50px; border-radius: 25px;
    border: 2px solid rgba(255,255,255,0.8); background: rgba(20,20,22,0.55);
    box-shadow: inset 0 0 0 2px rgba(120,120,120,0.5);
    display: flex; align-items: center; justify-content: center;
    font-size: 14px; font-style: italic; color: var(--white);
  }
  .consent { margin-top: 18px; display: flex; align-items: center; gap: 9px; font-size: 13.5px; font-style: italic; }
  .consent-box { width: 12px; height: 12px; background: var(--white); border-radius: 2px; display: flex; align-items: center; justify-content: center; }
  .submit-btn {
    margin-top: 16px; width: 207px; height: 47px; border-radius: 24px; background: var(--cta-orange);
    color: var(--white); font-weight: 700; font-size: 15px; letter-spacing: 0.5px;
    display: flex; align-items: center; justify-content: center;
  }

  .stats { position: absolute; left: 0; top: 561px; width: 1200px; height: 167px; }
  .stat { position: absolute; top: 44px; width: 220px; margin-left: -110px; text-align: center; }
  .stat-value { font-size: 38px; font-weight: 900; color: var(--ink); line-height: 1; }
  .stat-label { margin-top: 12px; font-size: 14.5px; color: var(--accent-blue); line-height: 1.35; }

  .site-footer { position: absolute; left: 0; top: 728px; width: 1200px; height: 125px; background: var(--brand-blue); color: var(--white); }
  .footer-nav { position: absolute; left: 75px; top: 34px; display: flex; gap: 0; }
  .footer-nav a { color: var(--white); text-decoration: none; font-size: 13px; font-weight: 700; }
  .copyright { position: absolute; left: 75px; top: 62px; font-size: 12px; line-height: 1.65; }
  .site-footer .brand { left: 557px; top: 38px; width: 86px; }
  .site-footer .brand-dot { background: var(--white); }
  .follow { position: absolute; left: 960px; top: 34px; }
  .follow-title { font-size: 13px; font-weight: 700; }
  .social-list { display: flex; gap: 18px; margin-top: 16px; }
  .social-item { width: 18px; height: 18px; border-radius: 50%; background: var(--white); }
</style>
</head>
<body>
  <section class="hero">
    <div class="hero-photo" role="img" aria-label="Shopper in a supermarket aisle pushing a trolley while checking a phone, shelves blurred behind"></div>
    <div class="hero-shade"></div>

    <div class="brand">
      <span class="brand-dot"></span>
      <span class="brand-name">plumora</span>
    </div>

    <nav class="main-nav">
      <a href="#about">ABOUT</a>
      <a href="#results">RESULTS</a>
      <a href="#how">HOW</a>
      <a href="#trial" class="nav-trial">FREE TRIAL</a>
    </nav>

    <form class="signup">
      <h1 class="signup-title">START HERE</h1>
      <div class="email-field">Enter Email Address</div>
      <label class="consent">
        <span class="consent-box">
          <svg width="9" height="8" viewBox="0 0 9 8"><path d="M1 4.2 L3.4 6.4 L8 1.4" fill="none" stroke="#2a2a2e" stroke-width="1.8"/></svg>
        </span>
        Yes, I have read and agree to the Privacy Policy and agree to receive email marketing from Plumora88
      </label>
      <div class="submit-btn">SUBMIT</div>
    </form>
  </section>

  <section class="stats">
    <div class="stat" style="left:197px;">
      <div class="stat-value">2.2M</div>
      <div class="stat-label">Photo Reviews<br>Last Year</div>
    </div>
    <div class="stat" style="left:465px;">
      <div class="stat-value">5P</div>
      <div class="stat-label">From Per Photo<br>Review</div>
    </div>
    <div class="stat" style="left:736px;">
      <div class="stat-value">97.2%</div>
      <div class="stat-label">Average Compliance</div>
    </div>
    <div class="stat" style="left:1007px;">
      <div class="stat-value">3-8%</div>
      <div class="stat-label">Sales Increase</div>
    </div>
  </section>

  <footer class="site-footer">
    <nav class="footer-nav">
      <a href="#about" style="width:72px;">ABOUT</a>
      <a href="#results" style="width:80px;">RESULTS</a>
      <a href="#how" style="width:71px;">HOW</a>
      <a href="#trial">FREE TRIAL</a>
    </nav>
    <p class="copyright">Copyright © 2018. Company Name.<br>All Right Reserved</p>

    <div class="brand">
      <span class="brand-dot"></span>
      <span class="brand-name">plumora</span>
    </div>

    <div class="follow">
      <div class="follow-title">FOLLOW US</div>
      <div class="social-list">
        <span class="social-item"></span>
        <span class="social-item"></span>
        <span class="social-item"></span>
        <span class="social-item"></span>
        <span class="social-item"></span>
      </div>
    </div>
  </footer>
</body>
</html>
```